Spring Detox sale graphics for social media

You MUST read the Brief in the WORD document and follow the instructions there. I want to create 10 social media graphics (new Instagram size 4:5 (1080 x 1350 pixels) focusing on our Mother’s Day Spring Detox Sale graphics, using any of the pics attached. Use the attached pics, NO RANDOM STOCK PHOTOGRAPHY. For the color scheme of the graphics, they should all be complementary to the product colors or feel like Spring time.

Target Market(s)

primarily women

Requirements
Must have
• the photos and text attached

```html
<!DOCTYPE html>
<html lang="en">
<head>
<meta charset="utf-8">
<title>Mother's Day Spring Detox Sale</title>
<link href="https://fonts.googleapis.com/css2?family=Anton&family=Dancing+Script:wght@700&family=Oswald:wght@700&display=swap" rel="stylesheet">
<style>
  :root {
    --page: #fbf5e8;
    --meadow: #f4e2b4;
    --frame: #ffffff;
    --paper: #f7e5b8;
    --grid: rgba(232, 150, 130, 0.28);
    --rose: #c9669b;
    --plum: #7b4670;
    --white: #ffffff;
  }
  * { margin: 0; padding: 0; box-sizing: border-box; }
  html, body { width: 960px; height: 1200px; overflow: hidden; background: var(--page); }
  .canvas { position: relative; width: 960px; height: 1200px; background: var(--page); }
  .spring-backdrop {
    position: absolute; left: 18px; top: 18px; width: 924px; height: 1165px;
    background:
      radial-gradient(circle at 12% 30%, rgba(190, 190, 130, 0.55), transparent 28%),
      radial-gradient(circle at 90% 20%, rgba(236, 190, 160, 0.55), transparent 26%),
      radial-gradient(circle at 88% 75%, rgba(190, 190, 130, 0.5), transparent 28%),
      radial-gradient(circle at 15% 85%, rgba(236, 190, 160, 0.45), transparent 26%),
      var(--meadow);
  }
  .poster-frame {
    position: absolute; left: 99px; top: 91px; width: 761px; height: 1018px;
    background: var(--frame);
    box-shadow: 0 8px 28px rgba(60, 50, 30, 0.35);
  }
  .grid-paper {
    position: absolute; left: 11px; top: 10px; width: 741px; height: 997px;
    background-color: var(--paper);
    background-image:
      linear-gradient(var(--grid) 1px, transparent 1px),
      linear-gradient(90deg, var(--grid) 1px, transparent 1px);
    background-size: 13px 13px;
  }
  .headline { position: absolute; left: 0; top: 0; width: 960px; height: 1200px; }
  .sparkle { fill: var(--rose); }
  .mothers-day { font-family: "Oswald", sans-serif; font-weight: 700; font-size: 50px; fill: var(--rose); }
  .spring-script { font-family: "Dancing Script", cursive; font-weight: 700; font-size: 150px; fill: var(--rose); }
  .swoosh { fill: none; stroke: var(--rose); stroke-width: 4; stroke-linecap: round; }
  .ribbon { fill: var(--plum); }
  .ribbon-text { font-family: "Anton", sans-serif; font-size: 46px; fill: var(--white); letter-spacing: 1px; }
  .offer { font-family: "Anton", sans-serif; font-size: 110px; fill: var(--rose); }
  .product-lineup {
    position: absolute; left: 184px; top: 776px; width: 595px; height: 254px;
    border-radius: 18px;
    background: linear-gradient(90deg, #f3eef2 0%, #f7eded 35%, #eef3f1 65%, #eceef7 100%);
  }
</style>
</head>
<body>
<main class="canvas">
  <div class="spring-backdrop" role="img" aria-label="Soft spring leaves and petals scattered around the edges"></div>
  <section class="poster-frame">
    <div class="grid-paper"></div>
  </section>

  <svg class="headline" viewBox="0 0 960 1200" xmlns="http://www.w3.org/2000/svg">
    <defs>
      <path id="arc-mothers-day" d="M392 236 Q 540 150 690 258"/>
    </defs>
    <path class="sparkle" d="M306 158 Q309 178 326 181 Q309 184 306 204 Q303 184 286 181 Q303 178 306 158 Z"/>
    <path class="sparkle" d="M336 158 Q338 168 346 170 Q338 172 336 182 Q334 172 326 170 Q334 168 336 158 Z"/>
    <path class="sparkle" d="M331 186 Q333 196 341 198 Q333 200 331 210 Q329 200 321 198 Q329 196 331 186 Z"/>

    <text class="mothers-day"><textPath href="#arc-mothers-day" startOffset="50%" text-anchor="middle">Mother’s Day</textPath></text>
    <path class="swoosh" d="M440 246 Q 560 205 654 262"/>
    <text class="spring-script" x="272" y="322" textLength="420" lengthAdjust="spacingAndGlyphs">Spring</text>

    <polygon class="ribbon" points="302,337 657,337 640,376 657,415 302,415 319,376"/>
    <text class="ribbon-text" x="480" y="396" text-anchor="middle" textLength="258" lengthAdjust="spacingAndGlyphs">DETOX SALE</text>

    <text class="offer" x="258" y="576" textLength="418" lengthAdjust="spacingAndGlyphs" transform="rotate(-3 467 530)">25% OFF</text>
    <text class="offer" x="190" y="692" textLength="583" lengthAdjust="spacingAndGlyphs" transform="rotate(-2 481 645)">EVERYTHING!</text>
  </svg>

  <div class="product-lineup" role="img" aria-label="Photo of four supplement bottles: Liver Bloom, Tummy Bloom, Hormone Bloom and Sugar Bloom"></div>
</main>
</body>
</html>
```